Business Identity Stationary

Already have the logo which is in the attached files so only need the Business STationary
1) Double Sided Business Card
2) Letterhead
3) Presentation folder with business card holder on inside cover
4) WIth compliments slip
See information for business cards, letterhead and presentation folder below.

This should be a simply job using a logo we already had designed along with a little device. I suggest using the device off center and perhaps lower in the corner in an abstract way. Also the logo device could be used as a watermark for the letterhead. The designer who created the logo presented something that I think works well for a business card. The front of the double sided business card could have the name logo small for the website address and only use the Lime device on the front. Then on the back could be the name Barrow Advisory logo.

Please note that for the business card the black and lime green background do look good. Also please think of using the lime device separately in an unusual way.

It has been brought to my attention that.my budget was far to low. Hopefully this.will attract you to the project. 

The parent company of Barrow Advisory is TallHeron holdings. I have uploaded a file of the Tall Heron business card I really like. Perhaps use this business card as a guide to the type of modern and clean style I am looking for. It also works to have the Barrow Advisroy and Tall Heron similar.

Reason: Still haven't received anything exactly right.

Industry/Entity Type

Business

Font styles to use
Sans Serif

Colors
9bcb3c
000000
5c5c5c
add136
cadf82
eaf2cf
f9fbf2
1b1b1b
757575

Requirements
Must have
• 1) Double Sided Business Card
Marta Kellendorf
Director
Tel: +505 8264 3170
Email: mk@barrowadvisory-example.com
Website: www.barrowadvisory-example.com

Frederick Kellendorf
Director
Tel: +505 8264 3172
Email: fk@barrowadvisory-example.com

Lucia Brenes Otaduy
Director
Tel: 8642 1093
Email: lbo@barrowadvisory-example.com

2) Letterhead
Logo
Lime Logo Device
Website Address: www.barrowadvisory-example.com
Small print on bottom: Barrow Advisory a Tall Heron Holding Company SA. RUC J0487000239518

3) Presentation Folder
Traditional Presentation folder with inside front cover spot for the insertion of business card.

4) With Compliments slip

```html
<!DOCTYPE html>
<html lang="en">
<head>
<meta charset="utf-8">
<title>Barrow Advisory – Business Card</title>
<link rel="stylesheet" href="https://fonts.googleapis.com/css2?family=Questrial&display=swap">
<style>
  :root {
    --lime: #9bcb3c;
    --black: #1b1b1b;
    --grey-dark: #5c5c5c;
    --grey: #757575;
    --grey-light: #9a9a9a;
    --card-front: #eaf2cf;
    --card-back: #ffffff;
    --backdrop: #eeeeee;
  }
  * { box-sizing: border-box; margin: 0; padding: 0; }
  html, body {
    width: 1200px;
    height: 1000px;
    overflow: hidden;
    background: var(--backdrop);
    font-family: "Questrial", "Century Gothic", sans-serif;
  }
  .canvas { position: relative; width: 1200px; height: 1000px; }

  .card {
    position: absolute;
    left: 237px;
    width: 725px;
    height: 360px;
    border-radius: 40px;
    box-shadow: 0 2px 10px rgba(0,0,0,0.12);
  }
  .card--front { top: 80px; background: var(--card-front); }
  .card--back  { top: 530px; background: var(--card-back); }

  /* Front: brand name centred */
  .brand {
    display: flex;
    align-items: center;
    gap: 16px;
    color: var(--black);
    white-space: nowrap;
  }
  .brand__dot {
    border-radius: 50%;
    background: var(--lime);
    flex: none;
  }
  .card--front .brand {
    position: absolute;
    left: 50%;
    top: 50%;
    transform: translate(-50%, -50%);
    font-size: 54px;
    letter-spacing: 1px;
  }
  .card--front .brand__dot { width: 42px; height: 42px; }

  /* Back */
  .card--back .brand {
    position: absolute;
    left: 57px;
    top: 42px;
    font-size: 28px;
    gap: 10px;
  }
  .card--back .brand__dot { width: 18px; height: 18px; }

  .person {
    position: absolute;
    left: 58px;
    top: 112px;
  }
  .person__name {
    font-size: 27px;
    letter-spacing: 2px;
    color: var(--grey-dark);
  }
  .person__role {
    font-size: 15px;
    letter-spacing: 1px;
    color: var(--grey-light);
    margin-top: 2px;
  }

  .contact {
    position: absolute;
    left: 366px;
    top: 124px;
    list-style: none;
    font-size: 19px;
    letter-spacing: 1px;
    color: var(--grey-dark);
  }
  .contact__item {
    display: flex;
    align-items: center;
    gap: 4px;
    height: 29px;
  }
  .contact__icon { width: 18px; height: 20px; flex: none; }

  .legal {
    position: absolute;
    left: 0;
    right: 0;
    top: 224px;
    text-align: center;
    font-size: 15.5px;
    letter-spacing: 1.6px;
    line-height: 23px;
    color: var(--grey);
  }
  .website {
    position: absolute;
    left: 0;
    right: 0;
    top: 275px;
    text-align: center;
    font-size: 20px;
    font-weight: 700;
    letter-spacing: 1.5px;
    color: var(--grey-dark);
    -webkit-text-stroke: 0.4px var(--grey-dark);
  }
</style>
</head>
<body>
<main class="canvas">

  <section class="card card--front" aria-label="Business card front">
    <div class="brand">
      <span class="brand__dot"></span>
      <span class="brand__name">Barrow Advisory</span>
    </div>
  </section>

  <section class="card card--back" aria-label="Business card back">
    <div class="brand">
      <span class="brand__dot"></span>
      <span class="brand__name">Barrow Advisory</span>
    </div>

    <div class="person">
      <p class="person__name">Marta Kellendorf</p>
      <p class="person__role">Director</p>
    </div>

    <ul class="contact">
      <li class="contact__item">
        <svg class="contact__icon" viewBox="0 0 18 20" aria-hidden="true">
          <rect x="4" y="1" width="10" height="18" rx="1.5" fill="none" stroke="var(--lime)" stroke-width="1.6"/>
          <line x1="7.5" y1="16" x2="10.5" y2="16" stroke="var(--lime)" stroke-width="1.4"/>
        </svg>
        <span>+505 8264 3170</span>
      </li>
      <li class="contact__item">
        <svg class="contact__icon" viewBox="0 0 18 20" aria-hidden="true">
          <rect x="1" y="5" width="16" height="11" rx="1" fill="var(--lime)"/>
          <polyline points="1.5,5.5 9,11.5 16.5,5.5" fill="none" stroke="#ffffff" stroke-width="1.2"/>
        </svg>
        <span>mk@barrowadvisory-example.com</span>
      </li>
    </ul>

    <p class="legal">
      Barrow Advisory a Tall Heron Holding Company SA.<br>
      RUC J0487000239518
    </p>
    <p class="website">www.barrowadvisory-example.com</p>
  </section>

</main>
</body>
</html>
```